Website redesign www.marigoldlawpc.com law firm site

Need to redesign the website that I currently have to look more modern and professional. Would also like to be able to make updates and post without having a huge hassle. See current www.marigoldlawpc.com. I just think that it looks very immature and it's very templated there's no ability for me to make posts or Add links or anything like that

Target Market(s)

California people looking for a powerhouse attorney in

Industry/Entity Type

Legal

Number of Pages Required

3 page

Font styles to use
Serif
Sans Serif

Colors
ec1f27
000000
ffffff

Requirements
Must have
• Must be mobile friendly. Must look professional and have ability to post links to other websites. Must have ability to post blogs or articles. Would like to be able to read my FeeTrove account and also have the ability to upload forms for people to download
Nice to have
• Simple design easy to use and not cluttered with too much text

```html
<!DOCTYPE html>
<html lang="en">
<head>
<meta charset="utf-8">
<title>Marigold Law, P.C. | Chico California Attorney</title>
<link href="https://fonts.googleapis.com/css2?family=Noto+Serif:ital,wght@0,400;0,700;1,400&family=Open+Sans:ital,wght@0,400;0,600;1,400&display=swap" rel="stylesheet">
<style>
:root{
  --red:#ec1f27;
  --red-deep:#d91a22;
  --black:#000000;
  --white:#ffffff;
  --ink:#2b2b2b;
  --text:#555555;
  --muted:#8a8a8a;
  --navy:#27365a;
  --light:#f3f3f3;
  --footer:#2c2c2c;
  --footer-dark:#1b1b1b;
  --footer-note:#353535;
  --serif:"Noto Serif",Georgia,serif;
  --sans:"Open Sans",Arial,sans-serif;
}
*{margin:0;padding:0;box-sizing:border-box}
html,body{width:1200px;height:2804px;overflow:hidden}
body{position:relative;font-family:var(--sans);color:var(--text);background:var(--white)}
.abs{position:absolute}
section,header,footer{position:absolute;left:0;width:1200px}

/* header */
.site-header{top:0;height:116px;background:var(--white);z-index:3}
.brand{left:99px;top:28px;font-family:var(--serif);font-size:34px;color:var(--red);font-weight:400;letter-spacing:.5px}
.top-contact{top:22px;font-size:14px;color:#555;display:flex;align-items:center;gap:10px}
.top-contact .ring{width:26px;height:26px;border:1.5px solid var(--red);border-radius:50%;display:flex;align-items:center;justify-content:center}
.main-nav{right:97px;top:70px;display:flex;gap:28px;font-family:var(--serif);font-size:14px;color:#444;align-items:center}
.main-nav .active{border:1.5px solid var(--red);color:var(--red);padding:3px 14px;border-radius:2px}

/* hero */
.hero{top:116px;height:566px;background:linear-gradient(100deg,#3b2a1c 0%,#6b4d31 35%,#8a6a47 55%,#4a3a2e 75%,#d9d2c8 100%)}
.hero-title{left:99px;top:224px;font-family:var(--serif);font-weight:700;font-size:40px;color:var(--white);letter-spacing:.5px}
.hero-text{left:99px;top:258px;width:390px;font-size:13.5px;line-height:22px;color:var(--white)}
.hero-btn{left:99px;top:317px;width:142px;height:36px;background:var(--red);color:var(--white);font-size:13px;display:flex;align-items:center;justify-content:center;border-radius:2px}
.arrow{top:278px;width:34px;height:34px;border-radius:50%;background:#111;display:flex;align-items:center;justify-content:center}

/* practice areas */
.practice{top:620px;height:473px}
.section-title{width:1200px;text-align:center;font-family:var(--serif);font-weight:700;font-size:32px;letter-spacing:.5px}
.practice .section-title{top:40px;color:var(--white)}
.card{top:180px;width:232px;height:239px;background:var(--white);box-shadow:0 2px 6px rgba(0,0,0,.15);text-align:center}
.card .icon{position:absolute;left:64px;top:-66px;width:104px;height:104px;border-radius:50%;background:#8c8c8c;border:6px solid #e9e9e9;display:flex;align-items:center;justify-content:center}
.card h3{margin-top:68px;font-family:var(--serif);font-weight:400;font-size:19px;color:#333}
.card p{margin:14px 18px 0;font-size:12px;line-height:20px;color:#666;height:78px;overflow:hidden}
.card .more{position:absolute;left:18px;right:18px;bottom:16px;border-top:1px solid #e5e5e5;padding-top:14px;font-size:11.5px;color:#777;letter-spacing:.5px}

/* about */
.about{top:1093px;height:412px}
.about-art{left:121px;top:51px;width:393px;height:299px;background:radial-gradient(ellipse at center,#7a1a1a 0%,#a8473a 40%,#e9e2dc 80%,#ffffff 100%)}
.about-title{left:564px;top:60px;font-family:var(--serif);font-weight:700;font-size:34px;color:var(--navy);letter-spacing:.5px}
.about-sub{left:564px;top:106px;font-family:var(--serif);font-size:20px;color:var(--navy)}
.about-text{left:564px;top:140px;width:540px;font-size:11.8px;line-height:21px;color:#555}
.about-list{top:281px;list-style:none;font-size:11.8px;line-height:23px;color:#444}
.about-list li{display:flex;align-items:center;gap:10px}

/* reviews */
.reviews{top:1505px;height:327px;background:var(--light)}
.reviews .section-title{top:38px;color:#333}
.rule{left:570px;width:60px;height:2px;background:var(--red)}
.avatar{top:121px;width:120px;height:120px;border-radius:50%;background:linear-gradient(160deg,#c9a58a,#8a6a55);border:4px solid #e6d7c4}
.review-title{top:124px;font-family:var(--serif);font-size:19px;color:#333}
.review-quote{top:156px;width:330px;font-style:italic;font-size:12px;line-height:20px;color:#555}
.review-author{top:228px;font-style:italic;font-size:13px;line-height:20px;color:#666}
.quote-mark{top:215px;font-family:var(--serif);font-size:80px;line-height:80px;color:#d9d9d9}

/* blog */
.blog{top:1832px;height:514px}
.blog .section-title{top:40px;color:#333}
.post{top:125px;width:308px}
.post .thumb{position:relative;width:308px;height:189px}
.post .date{position:absolute;left:0;bottom:0;width:48px;height:54px;background:rgba(40,40,40,.85);color:var(--white);text-align:center;padding-top:8px}
.post .date b{display:block;font-size:18px;font-weight:600;line-height:20px}
.post .date span{font-size:10px}
.post h4{margin-top:22px;font-family:var(--serif);font-weight:400;font-size:19px;color:#222}
.post p{margin-top:8px;font-size:11.8px;line-height:21px;color:#666}
.post .more{margin-top:14px;font-size:12px;color:#333;display:flex;align-items:center;gap:6px}

/* footer */
.site-footer{top:2346px;height:458px;background:var(--footer);color:var(--white)}
.footer-brand{left:99px;top:46px;font-family:var(--serif);font-size:30px;color:var(--white)}
.contact-list{left:99px;top:104px;list-style:none;font-size:13px;line-height:31px}
.contact-list li{display:flex;align-items:center;gap:14px}
.footer-head{top:46px;font-family:var(--serif);font-size:18px;color:var(--white)}
.quick-links{left:413px;top:88px;list-style:none;font-size:12px;line-height:25.6px}
.quick-links li{display:flex;align-items:center;gap:12px}
.news-text{left:634px;top:86px;width:250px;font-size:12px;line-height:21px}
.news-input{left:634px;top:134px;width:246px;height:38px;background:var(--white);color:#555;font-size:11px;padding:12px 12px}
.news-btn{left:634px;top:185px;width:90px;height:34px;background:var(--red);font-size:11px;display:flex;align-items:center;justify-content:center}
.copyright{top:286px;height:60px;width:1200px;background:var(--footer-dark);font-size:12px;display:flex;align-items:center;justify-content:center}
.footer-note{top:346px;height:112px;width:1200px;background:var(--footer-note);padding:24px 99px 0;font-size:10.5px;line-height:21px;color:#bdbdbd}
</style>
</head>
<body>

<header class="site-header">
  <div class="abs brand">Marigold Law, P.C.</div>
  <div class="abs top-contact" style="left:632px">
    <span class="ring"><svg width="13" height="13" viewBox="0 0 24 24"><path fill="#ec1f27" d="M6.6 10.8a15.1 15.1 0 006.6 6.6l2.2-2.2c.3-.3.7-.4 1-.2 1.1.4 2.3.6 3.6.6.6 0 1 .4 1 1V20c0 .6-.4 1-1 1A17 17 0 013 4c0-.6.4-1 1-1h3.5c.6 0 1 .4 1 1 0 1.3.2 2.5.6 3.6.1.3 0 .7-.2 1z"/></svg></span>
    Call Us (530) 555-0142
  </div>
  <div class="abs top-contact" style="left:846px">
    <span class="ring"><svg width="13" height="13" viewBox="0 0 24 24"><path fill="none" stroke="#ec1f27" stroke-width="2" d="M3 6h18v12H3zM3 6l9 7 9-7"/></svg></span>
    elena@marigoldlawgroup.com
  </div>
  <nav class="abs main-nav">
    <span class="active">Home</span><span>Attorney Profile</span><span>Practice Areas</span><span>Client Reviews</span><span>Links</span><span>Contact Us</span>
  </nav>
</header>

<section class="hero" role="img" aria-label="Photo of an attorney in a suit reading a book in a law library">
  <div class="abs arrow" style="left:34px"><svg width="12" height="12" viewBox="0 0 12 12"><path d="M8 1L3 6l5 5" fill="none" stroke="#fff" stroke-width="2"/></svg></div>
  <div class="abs arrow" style="left:1137px"><svg width="12" height="12" viewBox="0 0 12 12"><path d="M4 1l5 5-5 5" fill="none" stroke="#fff" stroke-width="2"/></svg></div>
</section>
<div class="abs hero-title" style="top:314px;z-index:2">MARIGOLD LAW, P.C.</div>
<div class="abs hero-text" style="top:370px;z-index:2">Marigold Law P.C. is owned by Elena M. Hart, a dedicated and caring professional who uses her broad range</div>
<div class="abs hero-btn" style="top:433px;z-index:2">READ MORE INFO</div>

<section class="practice">
  <svg class="abs" style="left:0;top:0" width="1200" height="473" viewBox="0 0 1200 473">
    <path d="M0 22 Q600 -20 1200 22 L1200 473 L0 473 Z" fill="#ec1f27"/>
    <path d="M0 22 Q600 -20 1200 22 L1200 60 Q600 20 0 60 Z" fill="#d91a22" opacity=".5"/>
  </svg>
  <h2 class="abs section-title" style="top:40px">PRACTICE AREAS</h2>

  <div class="abs card" style="left:99px">
    <div class="icon"><svg width="44" height="44" viewBox="0 0 44 44" fill="#fff"><circle cx="12" cy="12" r="5"/><circle cx="32" cy="12" r="5"/><rect x="6" y="19" width="12" height="14" rx="3"/><rect x="26" y="19" width="12" height="14" rx="3"/><rect x="16" y="28" width="12" height="10"/></svg></div>
    <h3>Business Law</h3>
    <p>Small and medium-sized businesses have many of the same legal issues that affect large businesses, such as business structure, contracts, dispute</p>
    <div class="more">READ MORE</div>
  </div>
  <div class="abs card" style="left:355px">
    <div class="icon"><svg width="46" height="46" viewBox="0 0 46 46"><path d="M4 22 L23 6 L42 22" fill="none" stroke="#fff" stroke-width="4"/><path d="M10 20 V40 H36 V20" fill="none" stroke="#fff" stroke-width="3"/><path d="M23 22 V36 M16 26 H30 M14 32 L16 26 L18 32 Z M28 32 L30 26 L32 32 Z" fill="#fff" stroke="#fff" stroke-width="1.5"/></svg></div>
    <h3>Real Estate Law</h3>
    <p>At Marigold Law P.C., we help Californians who need legal advice and representation for Real Estate Law activities, such as closings,</p>
    <div class="more">READ MORE</div>
  </div>
  <div class="abs card" style="left:610px">
    <div class="icon"><svg width="44" height="44" viewBox="0 0 44 44" fill="#fff"><circle cx="15" cy="9" r="5"/><circle cx="30" cy="16" r="4"/><path d="M9 16h12l-2 12h-2v12h-4V28H11z"/><path d="M26 22h8v10h-2v8h-4v-8h-2z"/><path d="M6 6 Q22 -4 38 6" fill="none" stroke="#fff" stroke-width="2"/></svg></div>
    <h3>Family Law</h3>
    <p>Family Law is one area of legal concern that brings many people in to see our experienced Chico Family Law Attorney at Marigold Law P.C. Issues that</p>
    <div class="more">READ MORE</div>
  </div>
  <div class="abs card" style="left:866px">
    <div class="icon"><svg width="44" height="44" viewBox="0 0 44 44" fill="#fff"><circle cx="13" cy="8" r="4"/><circle cx="31" cy="10" r="4"/><path d="M10 14h6l3 10-3 2-1 14h-3l1-14-4-3zM28 16h6l2 10-3 1v13h-3V27l-4-2z"/><rect x="18" y="20" width="8" height="3"/></svg></div>
    <h3>Criminal Law</h3>
    <p>If you were charged with a criminal offense, or if you are under investigation for one, it is essential to hire an experienced, qualified attorney</p>
    <div class="more">READ MORE</div>
  </div>
</section>

<section class="about">
  <div class="abs about-art" role="img" aria-label="Word cloud illustration of legal terms centred on the words criminal law"></div>
  <h2 class="abs about-title">MARIGOLD LAW, P.C.</h2>
  <div class="abs about-sub">Chico California Attorney</div>
  <p class="abs about-text">Find the big firm style legal counsel you can work with in your hometown region at Marigold Law P.C., in Chico, CA. Attorney Elena M. Hart, Esq., offers a boutique law firm opportunity for clients who want to enjoy all the advantages of her broad legal experience and education. She works closely with clients, and has the knowledge of many areas of law to apply to your situation. This is very helpful when it is necessary to incorporate those different areas of law practice into creating a winning argument for your unique case.</p>
  <ul class="abs about-list" style="left:564px">
    <li><svg width="10" height="10" viewBox="0 0 10 10"><circle cx="5" cy="5" r="4.3" fill="none" stroke="#333"/><path d="M4 3l2 2-2 2" fill="none" stroke="#333"/></svg>Business Law</li>
    <li><svg width="10" height="10" viewBox="0 0 10 10"><circle cx="5" cy="5" r="4.3" fill="none" stroke="#333"/><path d="M4 3l2 2-2 2" fill="none" stroke="#333"/></svg>Real Estate Law</li>
    <li><svg width="10" height="10" viewBox="0 0 10 10"><circle cx="5" cy="5" r="4.3" fill="none" stroke="#333"/><path d="M4 3l2 2-2 2" fill="none" stroke="#333"/></svg>Bankruptcy</li>
    <li><svg width="10" height="10" viewBox="0 0 10 10"><circle cx="5" cy="5" r="4.3" fill="none" stroke="#333"/><path d="M4 3l2 2-2 2" fill="none" stroke="#333"/></svg>Family Law</li>
  </ul>
  <ul class="abs about-list" style="left:762px">
    <li><svg width="10" height="10" viewBox="0 0 10 10"><circle cx="5" cy="5" r="4.3" fill="none" stroke="#333"/><path d="M4 3l2 2-2 2" fill="none" stroke="#333"/></svg>Criminal Law</li>
    <li><svg width="10" height="10" viewBox="0 0 10 10"><circle cx="5" cy="5" r="4.3" fill="none" stroke="#333"/><path d="M4 3l2 2-2 2" fill="none" stroke="#333"/></svg>Civil Litigation</li>
    <li><svg width="10" height="10" viewBox="0 0 10 10"><circle cx="5" cy="5" r="4.3" fill="none" stroke="#333"/><path d="M4 3l2 2-2 2" fill="none" stroke="#333"/></svg>Unlawful Detainer</li>
  </ul>
</section>

<section class="reviews">
  <h2 class="abs section-title">CUSTOMER REVIEWS</h2>
  <div class="abs rule" style="top:87px"></div>

  <div class="abs avatar" style="left:99px" role="img" aria-label="Portrait photo of a client"></div>
  <h3 class="abs review-title" style="left:239px;font-weight:400">A Vital Component</h3>
  <p class="abs review-quote" style="left:239px">“ Marigold Law is our go-to source for professional and sound legal advice.  Marigold Law has become a vital component to the success of our business as well as the businesses</p>
  <p class="abs review-author" style="left:239px">Ridgeline Accounting<br>Professionals</p>
  <div class="abs quote-mark" style="left:510px">”</div>

  <div class="abs avatar" style="left:630px" role="img" aria-label="Portrait photo of a client"></div>
  <h3 class="abs review-title" style="left:770px;font-weight:400">Exceeded Our Expectations</h3>
  <p class="abs review-quote" style="left:770px">“ Marigold Law has met and exceeded our expectations in assisting our company with our real estate legal needs. In an area of law where the rules our ever changing,</p>
  <p class="abs review-author" style="left:770px">Ridgeline Accounting<br>Professionals</p>
  <div class="abs quote-mark" style="left:1044px">”</div>
</section>

<section class="blog">
  <h2 class="abs section-title">LATEST BLOG</h2>
  <div class="abs rule" style="top:92px"></div>

  <article class="abs post" style="left:99px">
    <div class="thumb" role="img" aria-label="Photo of business people reviewing documents in an office" style="background:linear-gradient(135deg,#5b6b4a,#b9a98c 50%,#3c3f4a)">
      <div class="date"><b>02</b><span>JUN</span></div>
    </div>
    <h4>Lorem ipsum dolor sit amet,</h4>
    <p>Lorem ipsum dolor sit amet, consectetur adipiscing elit. Sed blandit massa vel mauris sollicitudin dignissim. Lorem ipsum dolor sit amet, consectetur</p>
    <div class="more">READ MORE <svg width="10" height="10" viewBox="0 0 10 10"><circle cx="5" cy="5" r="5" fill="#333"/><path d="M4 3l2 2-2 2" fill="none" stroke="#fff"/></svg></div>
  </article>
  <article class="abs post" style="left:445px">
    <div class="thumb" role="img" aria-label="Photo of hands signing papers at a meeting table" style="background:linear-gradient(135deg,#2a2c33,#c8ccd2 50%,#6e7278)">
      <div class="date"><b>02</b><span>JUN</span></div>
    </div>
    <h4>Lorem ipsum dolor sit amet,</h4>
    <p>Lorem ipsum dolor sit amet, consectetur adipiscing elit. Sed blandit massa vel mauris sollicitudin dignissim. Lorem ipsum dolor sit amet, consectetur</p>
    <div class="more">READ MORE <svg width="10" height="10" viewBox="0 0 10 10"><circle cx="5" cy="5" r="5" fill="#333"/><path d="M4 3l2 2-2 2" fill="none" stroke="#fff"/></svg></div>
  </article>
  <article class="abs post" style="left:791px">
    <div class="thumb" role="img" aria-label="Photo of a pen resting on a sealed certificate" style="background:linear-gradient(135deg,#1e1f22,#4a4c52 45%,#e8e6e2 70%,#f4f2ee)">
      <div class="date"><b>02</b><span>JUN</span></div>
    </div>
    <h4>Lorem ipsum dolor sit amet,</h4>
    <p>Lorem ipsum dolor sit amet, consectetur adipiscing elit. Sed blandit massa vel mauris sollicitudin dignissim. Lorem ipsum dolor sit amet, consectetur</p>
    <div class="more">READ MORE <svg width="10" height="10" viewBox="0 0 10 10"><circle cx="5" cy="5" r="5" fill="#333"/><path d="M4 3l2 2-2 2" fill="none" stroke="#fff"/></svg></div>
  </article>
</section>

<footer class="site-footer">
  <div class="abs footer-brand">Marigold Law</div>
  <ul class="abs contact-list">
    <li><svg width="14" height="14" viewBox="0 0 24 24"><path fill="#fff" d="M6.6 10.8a15.1 15.1 0 006.6 6.6l2.2-2.2c.3-.3.7-.4 1-.2 1.1.4 2.3.6 3.6.6.6 0 1 .4 1 1V20c0 .6-.4 1-1 1A17 17 0 013 4c0-.6.4-1 1-1h3.5c.6 0 1 .4 1 1 0 1.3.2 2.5.6 3.6.1.3 0 .7-.2 1z"/></svg>Call Us (530) 555-0142</li>
    <li><svg width="14" height="14" viewBox="0 0 24 24"><path fill="#fff" d="M6 2h10v6H6zM3 9h18v10h-3v3H6v-3H3zM8 15v5h8v-5z"/></svg>Fax: (888) 555-0178</li>
    <li><svg width="14" height="14" viewBox="0 0 24 24"><path fill="#fff" d="M2 5h20v14H2zM4 7l8 6 8-6" stroke="#2c2c2c" stroke-width="1.5"/></svg>Email: elena@marigoldlawgroup.com</li>
    <li><svg width="14" height="14" viewBox="0 0 24 24"><path fill="#fff" d="M12 2a7 7 0 00-7 7c0 5 7 13 7 13s7-8 7-13a7 7 0 00-7-7zm0 9.5A2.5 2.5 0 1112 6a2.5 2.5 0 010 5.5z"/></svg>Address: 480 Orchard Avenue</li>
    <li style="padding-left:28px">Suite 210 Chico, CA 95926</li>
  </ul>

  <h3 class="abs footer-head" style="left:413px;font-weight:400">QUICK LINKS</h3>
  <ul class="abs quick-links">
    <li><svg width="6" height="8" viewBox="0 0 6 8"><path d="M0 0l6 4-6 4z" fill="#fff"/></svg>HOME</li>
    <li><svg width="6" height="8" viewBox="0 0 6 8"><path d="M0 0l6 4-6 4z" fill="#fff"/></svg>ATTORNEY PROFILE</li>
    <li><svg width="6" height="8" viewBox="0 0 6 8"><path d="M0 0l6 4-6 4z" fill="#fff"/></svg>PRACTICE AREAS</li>
    <li><svg width="6" height="8" viewBox="0 0 6 8"><path d="M0 0l6 4-6 4z" fill="#fff"/></svg>CLIENT REVIEWS</li>
    <li><svg width="6" height="8" viewBox="0 0 6 8"><path d="M0 0l6 4-6 4z" fill="#fff"/></svg>LINKS</li>
    <li><svg width="6" height="8" viewBox="0 0 6 8"><path d="M0 0l6 4-6 4z" fill="#fff"/></svg>CONTACT US</li>
  </ul>

  <h3 class="abs footer-head" style="left:634px;font-weight:400">JOIN OUR NEWSLETTER</h3>
  <p class="abs news-text">Excepteur sint occaecat cupidatat non proident, sunt in culpa qui</p>
  <div class="abs news-input">Enter Name</div>
  <div class="abs news-btn">SUBSCRIBE</div>

  <div class="abs" style="left:940px;top:60px;width:160px;height:30px;background:#e8e8e8;border-radius:2px" aria-label="Listing badge"></div>
  <div class="abs" style="left:940px;top:120px;width:75px;height:75px;border-radius:50%;background:#d6d6d6" aria-label="Association badge"></div>
  <div class="abs" style="left:1028px;top:120px;width:75px;height:75px;border-radius:50%;background:#2f5f9e" aria-label="Rating badge"></div>
  <div class="abs" style="left:968px;top:211px;width:34px;height:34px;background:#3b5b9a;border-radius:3px" aria-label="Social link"></div>
  <div class="abs" style="left:1010px;top:211px;width:34px;height:34px;background:#1a7bb0;border-radius:3px" aria-label="Social link"></div>
  <div class="abs" style="left:1052px;top:211px;width:34px;height:34px;background:#2f6db5;border-radius:3px" aria-label="Social link"></div>

  <div class="abs copyright">© 2016 Marigold Law, P.C. .. All Rights Reserved.</div>
  <p class="abs footer-note">Marigold Law, P.C. provides experienced, compassionate legal guidance and representation to businesses and individuals in the areas of business law, real estate law, bankruptcy, family law, criminal law, civil litigation, unlawful detainer, and legal document preparation. Located in Chico, California, we serve clients throughout Northern California including Butte County, Tehama County, Plumas County, Glenn County, Colusa County, Sutter County, Yuba County, Sierra County and Nevada County</p>
</footer>

</body>
</html>
```